Business Card for Professional Photographer

I'm looking for an eye catching modern clean design that compliments my logo/ website fonts & colours.
I specialise in architecture, corporate & commercial photography so I'm marketing to professional clients rather than portrait / wedding clients.

I would prefer to not have a solid black design.

My logo brand guide is as follows :

Main front font. : Reislust
Main font colour : #fff
Slogan front font : Ubuntu Bold
Monogram front font : Venti Medium
Container colour : #fff

I need print ready files in pdf .png & .eps formats.

Included in the files below are some screen grabs as reference to font & colours etc.

```html
<!DOCTYPE html>
<html lang="en">
<head>
<meta charset="utf-8">
<title>Still Meridian – Business Card</title>
<link href="https://fonts.googleapis.com/css2?family=Ubuntu:wght@300;400;500&family=Roboto:wght@400&family=Saira+Semi+Condensed:wght@600&display=swap" rel="stylesheet">
<style>
  :root {
    --backdrop: #b9b9b9;
    --card-dark: #121212;
    --card-dark-2: #23211f;
    --card-light: #f4f4f2;
    --gold: #b8893a;
    --gold-light: #d9bd7a;
    --gold-text: #c49a52;
    --ink: #2a2a2a;
  }
  * { margin: 0; padding: 0; box-sizing: border-box; }
  html, body { width: 1200px; height: 576px; overflow: hidden; }
  body {
    background: var(--backdrop);
    position: relative;
    font-family: "Ubuntu", sans-serif;
  }
  .card {
    position: absolute;
    top: 138px;
    width: 484px;
    height: 294px;
    border-radius: 10px;
    overflow: hidden;
  }
  .card-front { left: 82px; background: var(--card-dark); }
  .card-back { left: 602px; background: var(--card-light); }

  .photo-collage {
    position: absolute;
    inset: 0;
    background: linear-gradient(135deg, var(--card-dark-2) 0%, var(--card-dark) 55%, #1b1c20 100%);
  }
  .brand-mark {
    position: absolute;
    display: flex;
    align-items: center;
  }
  .card-front .brand-mark { left: 98px; top: 126px; }
  .brand-ring { width: 48px; height: 48px; margin-right: 34px; }
  .brand-name {
    font-family: "Ubuntu", sans-serif;
    font-weight: 300;
    color: var(--gold-text);
    text-transform: uppercase;
    letter-spacing: 3px;
    white-space: nowrap;
  }
  .brand-tagline {
    font-family: "Ubuntu", sans-serif;
    font-weight: 500;
    color: var(--gold);
    letter-spacing: 2.2px;
    white-space: nowrap;
  }
  .card-front .brand-name { font-size: 22px; line-height: 24px; }
  .card-front .brand-tagline { font-size: 7.5px; margin-top: 5px; }
  .front-url {
    position: absolute;
    left: 192px;
    top: 320px;
  }
  .card-front .web-address {
    position: absolute;
    left: 138px;
    top: 286px;
    transform: translateY(-100%);
    font-size: 13px;
    letter-spacing: 1.8px;
    color: var(--gold-light);
  }

  .card-back .brand-block { position: absolute; left: 24px; top: 33px; }
  .card-back .brand-name { font-size: 22px; line-height: 24px; color: var(--gold); letter-spacing: 2.6px; }
  .card-back .brand-tagline { font-size: 7.5px; margin-top: 4px; }

  .person { position: absolute; left: 24px; top: 132px; }
  .person-name {
    font-family: "Saira Semi Condensed", sans-serif;
    font-weight: 600;
    font-size: 19px;
    line-height: 22px;
    color: var(--gold);
  }
  .person-role {
    font-family: "Roboto", sans-serif;
    font-size: 12.5px;
    color: var(--ink);
    margin-top: 2px;
  }
  .contact-list {
    position: absolute;
    left: 24px;
    top: 196px;
    list-style: none;
    font-family: "Roboto", sans-serif;
    font-size: 13px;
    color: var(--ink);
  }
  .contact-list li { display: flex; align-items: center; height: 18.5px; }
  .contact-icon { width: 11px; height: 11px; margin-right: 11px; }
  .contact-address { margin-top: 6px; }
  .contact-address span { padding-left: 0; }
  .address-line { margin-left: -0px; }

  .decor-ring { position: absolute; left: 330px; top: 40px; width: 200px; height: 260px; }
</style>
</head>
<body>

<section class="card card-front">
  <div class="photo-collage" role="img" aria-label="Dimmed collage of architecture, interior and commercial photographs"></div>
  <div class="brand-mark">
    <svg class="brand-ring" viewBox="0 0 48 48" aria-hidden="true">
      <circle cx="24" cy="24" r="21" fill="none" stroke="var(--gold-text)" stroke-width="3"/>
    </svg>
    <div>
      <div class="brand-name">Still Meridian</div>
      <div class="brand-tagline">Architecture Corporate Commercial</div>
    </div>
  </div>
  <div class="web-address">www.stillmeridian.com.au</div>
</section>

<section class="card card-back">
  <div class="brand-block">
    <div class="brand-name">Still Meridian</div>
    <div class="brand-tagline">Architecture Corporate Commercial</div>
  </div>

  <div class="person">
    <div class="person-name">Reid Callaway</div>
    <div class="person-role">Photographer</div>
  </div>

  <ul class="contact-list">
    <li>
      <svg class="contact-icon" viewBox="0 0 12 12" aria-hidden="true">
        <path d="M1 3.5C1 2 2.5 1.5 6 1.5S11 2 11 3.5L9 4.5 8.5 3.5h-5L3 4.5z M2.5 6h7l1 4.5h-9z" fill="var(--gold)"/>
      </svg>
      <span>0400517286</span>
    </li>
    <li>
      <svg class="contact-icon" viewBox="0 0 12 12" aria-hidden="true">
        <rect x="1" y="2.5" width="10" height="7" fill="var(--gold)"/>
        <path d="M1 2.5 6 6.5 11 2.5" fill="none" stroke="var(--card-light)" stroke-width="1"/>
      </svg>
      <span>hello@stillmeridian.com.au</span>
    </li>
    <li>
      <svg class="contact-icon" viewBox="0 0 12 12" aria-hidden="true">
        <circle cx="6" cy="6" r="5" fill="var(--gold-light)"/>
        <path d="M1 6h10M6 1c-2.5 3-2.5 7 0 10M6 1c2.5 3 2.5 7 0 10" fill="none" stroke="var(--gold)" stroke-width="0.8"/>
      </svg>
      <span>www.stillmeridian.com.au</span>
    </li>
    <li class="contact-address"><span>48 Ferris Rd Lakeview Vic 3199</span></li>
  </ul>

  <svg class="decor-ring" viewBox="0 0 200 260" aria-hidden="true">
    <defs>
      <linearGradient id="goldSweep" x1="0" y1="1" x2="1" y2="0">
        <stop offset="0" stop-color="#b07f2e"/>
        <stop offset="1" stop-color="#dcc37f"/>
      </linearGradient>
    </defs>
    <circle cx="88" cy="134" r="58" fill="none" stroke="url(#goldSweep)" stroke-width="9"/>
  </svg>
</section>

</body>
</html>
```